Refresh Brightpath Coursecraft

Need a new design for e-learning development and web app development site: http://brightpathcoursecraft.example. Need pages for everything on menu bar plus a training services and a web app development services pages and a better page for samples http://brightpathcoursecraft.example/samples5/.

***Must be programmed in html 5. NO CMS. No WP. No Plume. Straight html/css.

Target Market(s)

government

Industry/Entity Type

Government

Coding

Coded - Design and coding required

Number of Pages Required

1 page

Requirements
Must have
• Must be coded in html5/css. No CMS.
• Divided so you can easily see that we offer 3 separate services:
• Live Training - E-Learning Development - Web App Development
• A way to display logos of all our clients like on bottom of this page: https://www.quorvatests.example (this is also our website so you can copy all these logos)
• List both our Denver location which is already on our website plus our office in Velmoro Plaza. Street 62 Sur, 14-87. Medellín, Antioquia.
• A page like this for our web app dev services https://www.tekvanu.example/product-development
Should not have
• CMS

```html
<!DOCTYPE html>
<html lang="en">
<head>
<meta charset="utf-8">
<title>Brightpath Coursecraft</title>
<link href="https://fonts.googleapis.com/css2?family=Oswald:wght@400;500&family=Lato:wght@400;700&display=swap" rel="stylesheet">
<style>
:root{
  --orange:#f5a623;
  --orange-dark:#e8951a;
  --blue:#1d7fc1;
  --navy:#0d1b2a;
  --ink:#444a52;
  --grey-bg:#efefef;
  --white:#ffffff;
  --footer:#101215;
}
*{box-sizing:border-box;margin:0;padding:0}
html,body{width:1200px;height:3974px;overflow:hidden}
body{position:relative;background:var(--white);font-family:'Lato',sans-serif;color:var(--ink)}
.abs{position:absolute}
h1,h2,h3,.nav a,.btn{font-family:'Oswald',sans-serif}

/* hero */
.hero{left:0;top:0;width:1200px;height:720px;overflow:hidden}
.hero-photo{position:absolute;inset:0;background:linear-gradient(135deg,#2b3645 0%,#1a2634 40%,#3a4a5c 70%,#18222e 100%)}
.hero-shade{position:absolute;inset:0;background:rgba(8,20,35,.45)}
.brand{display:flex;align-items:center;gap:14px;color:var(--white);font-family:'Lato',sans-serif;font-weight:700;font-size:30px;letter-spacing:.5px}
.brand .dot{width:44px;height:44px;border-radius:50%;background:var(--orange)}
.hero .brand{left:106px;top:58px}
.nav{left:620px;top:66px;display:flex;gap:32px}
.nav a{color:var(--white);text-decoration:none;font-size:21px;font-weight:500}
.hero h1{left:0;width:1200px;top:282px;text-align:center;color:var(--white);font-size:50px;font-weight:500;line-height:62px}
.btn{display:inline-flex;align-items:center;justify-content:center;font-size:22px;text-decoration:none}
.btn-solid{left:490px;top:460px;width:220px;height:60px;background:var(--orange);color:#1a1a1a;border-radius:30px}
.hero-curve{left:0;top:600px}

/* about */
.about-photo{left:95px;top:795px;width:350px;height:350px;border-radius:50%;border:7px solid var(--blue);background:radial-gradient(circle at 45% 40%,#6d7580 0%,#3a3f47 55%,#23272d 100%)}
.section-title{color:var(--orange);font-weight:500}
.about h2{left:477px;top:800px;font-size:46px}
.about p{left:477px;top:880px;width:610px;font-size:15.5px;line-height:35px}
.btn-line{width:204px;height:62px;border:3px solid var(--orange);color:var(--orange);border-radius:4px}
.about .btn{left:477px;top:1080px}

/* services */
.services{left:0;top:1250px;width:1200px;height:1338px;background:var(--grey-bg)}
.services > h2{left:0;width:1200px;top:55px;text-align:center;font-size:46px}
.svc-photo{width:427px;height:289px;border-radius:4px}
.svc h3{color:var(--orange);font-size:36px;font-weight:500}
.svc p{width:510px;font-size:15.5px;line-height:33px}
.p1{left:90px;top:199px;background:linear-gradient(135deg,#e8e6e1,#c9c3b8 60%,#8d8a84)}
.s1 h3{left:577px;top:195px}.s1 p{left:577px;top:265px}.s1 .btn{left:580px;top:424px}
.p2{left:683px;top:596px;background:linear-gradient(135deg,#6f5a45,#b0a290 50%,#4f6f8a)}
.s2 h3{left:90px;top:592px}.s2 p{left:90px;top:662px;width:490px}.s2 .btn{left:90px;top:825px}
.p3{left:90px;top:991px;background:linear-gradient(135deg,#3b4c5e,#7a6456 55%,#2a333e)}
.s3 h3{left:577px;top:988px}.s3 p{left:577px;top:1058px}.s3 .btn{left:580px;top:1218px}

/* clients */
.clients h2{left:0;width:1200px;top:2660px;text-align:center;font-size:46px}
.client-row{left:60px;width:1080px;display:flex;justify-content:space-between;align-items:center}
.client{display:flex;align-items:center;gap:8px;font-size:17px;font-weight:700;color:#2f3b4a;white-space:nowrap}
.client i{display:block;width:26px;height:26px;border-radius:50%;background:#2f3b4a}
.r1{top:2830px}.r2{top:2962px}.r3{top:3088px}

/* footer */
.footer{left:0;top:3210px;width:1200px;height:764px;overflow:hidden}
.footer-bg{position:absolute;left:0;top:0;width:1200px;height:764px;background:linear-gradient(160deg,#191c21,#0b0c0e 60%,#1b1e22)}
.footer .brand{left:460px;top:92px}
.col{color:var(--white)}
.col h4{font-family:'Oswald',sans-serif;font-weight:500;font-size:20px;margin-bottom:26px}
.col li{list-style:none;font-size:15px;line-height:32px}
.col .row{display:flex;gap:16px;font-size:15px;line-height:26px;margin-bottom:6px}
.col svg{flex:none;margin-top:5px}
.c1{left:172px;top:240px}.c2{left:458px;top:240px;width:260px}.c3{left:776px;top:240px;width:300px}
.map{width:220px;height:130px;border-radius:4px;background:linear-gradient(135deg,#e9ecef,#d3d9df)}
.m1{left:458px;top:467px}.m2{left:783px;top:467px}
.footer-rule{left:0;top:658px;width:1200px;height:1px;background:rgba(255,255,255,.3)}
.legal{top:703px;color:var(--white);font-family:'Oswald',sans-serif;font-size:16px}
.copy{left:95px}
.legal-links{left:740px;display:flex;gap:44px}
</style>
</head>
<body>

<header class="hero abs">
  <div class="hero-photo" role="img" aria-label="Photo of a developer working at a desk with monitors showing code"></div>
  <div class="hero-shade"></div>
  <div class="brand abs"><span class="dot"></span>Brightpath Coursecraft</div>
  <nav class="nav abs"><a href="#">Home</a><a href="#">Portfolio</a><a href="#">Team &amp; Experience</a><a href="#">Contacts</a></nav>
  <h1 class="abs">We create engaging training that<br>exceed expectations.</h1>
  <a class="btn btn-solid abs" href="#">View More</a>
  <svg class="hero-curve abs" width="1200" height="120" viewBox="0 0 1200 120">
    <path d="M0 20 Q600 160 1200 0 L1200 120 L0 120 Z" fill="#fff"/>
    <path d="M0 20 Q600 160 1200 0" fill="none" stroke="#1d7fc1" stroke-width="8"/>
  </svg>
</header>

<section class="about">
  <div class="about-photo abs" role="img" aria-label="Photo of a hand using a tablet showing an e-learning screen"></div>
  <h2 class="section-title abs">About us</h2>
  <p class="abs">Brightpath Coursecraft is a HUBZone Certified, SBA 8(a) Certified, Native American Owned Small Disadvantaged Business located in Denver, Colorado. We have designed and delivered SCORM compliant eLearning, webinar, web-based training (WBT), instructor-led training (ILT), virtual ILT (vILT), blended, and 3D Immersive training courses.</p>
  <a class="btn btn-line abs" href="#">Read More</a>
</section>

<section class="services abs">
  <h2 class="section-title abs">Our Services</h2>
  <div class="svc s1">
    <div class="svc-photo p1 abs" role="img" aria-label="Photo of a woman with a headset taking notes at a laptop"></div>
    <h3 class="abs">Live Training</h3>
    <p class="abs">Lorem ipsum dolor sit amet, consectetur adipiscing elit. Etiam venenatis lacus quis laoreet rhoncus. Donec in ligula id sapien elementum commodo eu ac tortor. Morbi sit amet faucibus leo. Nunc semper risus ex, vitae bibendum diam bibendum et. Integer</p>
    <a class="btn btn-line abs" href="#">Read More</a>
  </div>
  <div class="svc s2">
    <div class="svc-photo p2 abs" role="img" aria-label="Photo of students working at computers in a library"></div>
    <h3 class="abs">E-Learning Development</h3>
    <p class="abs">Lorem ipsum dolor sit amet, consectetur adipiscing elit. Etiam venenatis lacus quis laoreet rhoncus. Donec in ligula id sapien elementum commodo eu ac tortor. Morbi sit amet faucibus leo. Nunc semper risus ex, vitae bibendum diam bibendum et.</p>
    <a class="btn btn-line abs" href="#">Read More</a>
  </div>
  <div class="svc s3">
    <div class="svc-photo p3 abs" role="img" aria-label="Photo of two developers pointing at code on a screen"></div>
    <h3 class="abs">Web App Development</h3>
    <p class="abs">Lorem ipsum dolor sit amet, consectetur adipiscing elit. Etiam venenatis lacus quis laoreet rhoncus. Donec in ligula id sapien elementum commodo eu ac tortor. Morbi sit amet faucibus leo. Nunc semper risus ex, vitae bibendum diam bibendum et. Integer</p>
    <a class="btn btn-line abs" href="#">Read More</a>
  </div>
</section>

<section class="clients">
  <h2 class="section-title abs">A Few of Our 75,000 Clients</h2>
  <div class="client-row r1 abs">
    <span class="client">Skyreach</span><span class="client"><i></i>Halden</span><span class="client"><i></i>Corvale</span><span class="client">Workpath</span><span class="client"><i></i>Ostrand</span><span class="client">CLAREVO</span><span class="client">Verdanel</span><span class="client">Redfell</span>
  </div>
  <div class="client-row r2 abs">
    <span class="client"><i></i>Marrow</span><span class="client">Ashcombe</span><span class="client">Univ. of Norwick</span><span class="client">Fibrolane</span><span class="client"><i></i>Kestley</span><span class="client"><i></i>Tarn</span>
  </div>
  <div class="client-row r3 abs">
    <span class="client"><i></i>Lindor</span><span class="client">Prairie State</span><span class="client">Ridgeway</span><span class="client"><i></i>Brisco</span><span class="client">Calder</span><span class="client"><i></i>Meriden</span><span class="client"><i></i>OVALITH</span>
  </div>
</section>

<footer class="footer abs">
  <div class="footer-bg" role="img" aria-label="Dark photo of people working at computers"></div>
  <svg class="abs" style="left:0;top:0" width="1200" height="120" viewBox="0 0 1200 120">
    <path d="M0 0 L1200 0 L1200 60 Q600 -20 0 100 Z" fill="#fff"/>
    <path d="M1200 60 Q600 -20 0 100" fill="none" stroke="#1d7fc1" stroke-width="8"/>
  </svg>
  <div class="brand abs"><span class="dot"></span>Brightpath Coursecraft</div>

  <div class="col c1 abs">
    <h4>Quick Links</h4>
    <ul><li>Home</li><li>Portfolio</li><li>Team &amp; Experience</li><li>Contacts</li></ul>
  </div>
  <div class="col c2 abs">
    <h4>Aurora</h4>
    <div class="row"><svg width="12" height="16" viewBox="0 0 12 16"><path d="M6 0a6 6 0 0 0-6 6c0 4.5 6 10 6 10s6-5.5 6-10a6 6 0 0 0-6-6zm0 8.5A2.5 2.5 0 1 1 6 3.5a2.5 2.5 0 0 1 0 5z" fill="#fff"/></svg><span>5870 E Larkspur Avenue,<br>Suite 2-115<br>Aurora, CO. 80012</span></div>
    <div class="row"><svg width="14" height="14" viewBox="0 0 14 14"><path d="M3 0l2.5 3.5-1.5 1.5c.8 1.8 2.2 3.2 4 4l1.5-1.5L13 10l-1.5 3C5.5 13 1 8.5 0 1.5z" fill="#fff"/></svg><span>Telephone: +1 555 014 7730</span></div>
    <div class="row"><svg width="16" height="12" viewBox="0 0 16 12"><rect x=".7" y=".7" width="14.6" height="10.6" fill="none" stroke="#fff" stroke-width="1.4"/><path d="M1 1l7 6 7-6" fill="none" stroke="#fff" stroke-width="1.4"/></svg><span style="font-size:13px">support@brightpathcoursecraft.example</span></div>
  </div>
  <div class="col c3 abs">
    <h4>Antioquia</h4>
    <div class="row"><svg width="12" height="16" viewBox="0 0 12 16"><path d="M6 0a6 6 0 0 0-6 6c0 4.5 6 10 6 10s6-5.5 6-10a6 6 0 0 0-6-6zm0 8.5A2.5 2.5 0 1 1 6 3.5a2.5 2.5 0 0 1 0 5z" fill="#fff"/></svg><span>Street 62 Sur, 14-87.<br>Medellín, Antioquia.</span></div>
    <div class="row"><svg width="14" height="14" viewBox="0 0 14 14"><path d="M3 0l2.5 3.5-1.5 1.5c.8 1.8 2.2 3.2 4 4l1.5-1.5L13 10l-1.5 3C5.5 13 1 8.5 0 1.5z" fill="#fff"/></svg><span>Telephone: +1 555 014 7730</span></div>
    <div class="row"><svg width="16" height="12" viewBox="0 0 16 12"><rect x=".7" y=".7" width="14.6" height="10.6" fill="none" stroke="#fff" stroke-width="1.4"/><path d="M1 1l7 6 7-6" fill="none" stroke="#fff" stroke-width="1.4"/></svg><span style="font-size:13px">support@brightpathcoursecraft.example</span></div>
  </div>
  <div class="map m1 abs" role="img" aria-label="Map of the Aurora office location"></div>
  <div class="map m2 abs" role="img" aria-label="Map of the Medellín office location"></div>

  <div class="footer-rule abs"></div>
  <div class="legal copy abs">© 2019 Brightpath Coursecraft. All Rights Reserved.</div>
  <div class="legal legal-links abs"><span>Terms &amp; Condition</span><span>Privacy Policy</span><span>Contact Us</span></div>
</footer>

</body>
</html>
```